New career and executive coaching business needs a business card design including logo

Company name: 'Bramblefield Growth Partners.' The aim of my coaching engagements is to help people improve their communication in the workplace and achieve their career goals. The process involves working with individuals to help them uncover their strengths and talents, then leverage those to improve their working lives. The Tarwick Inventory is the starting point to the process. I am after an exciting and interesting business card design (including logo)which is professional yet will still get people's attention.

Industry/Entity Type

Business

Contact Information for Business Card

Name: Malcolm Dervaney
Position: Owner
Address: 58 Quorrin Ct, Elmbridge Vic 3190
Phone: 0418923047
Website: bramblefieldgrowth.com.au
Email: malcolm@bgp.com.au

Colors
33a6d7
00a990
0355a3
3176b5

Requirements
Must have
• logo

```html
<!DOCTYPE html>
<html lang="en">
<head>
<meta charset="utf-8">
<title>Bramblefield Growth Partners – Business Card</title>
<link rel="stylesheet" href="https://fonts.googleapis.com/css2?family=Open+Sans:wght@400;600;700&display=swap">
<style>
  :root {
    --stage: #000000;
    --card-light: #f2f2f2;
    --teal: #00a88f;
    --teal-shade: #049e87;
    --teal-text: #13a594;
    --blue-deep: #0355a3;
    --ink: #3a3a3a;
    --white: #ffffff;
  }
  * { margin: 0; padding: 0; box-sizing: border-box; }
  html, body {
    width: 1200px; height: 900px; overflow: hidden;
    background: var(--stage);
    font-family: "Open Sans", Arial, sans-serif;
  }
  .canvas { position: relative; width: 1200px; height: 900px; }

  .card { position: absolute; top: 200px; width: 310px; height: 502px; overflow: hidden; }
  .card--front {
    left: 265px; background: var(--card-light);
    border-radius: 52px 0 52px 0;
  }
  .card--back {
    left: 641px; background: var(--teal);
    border-radius: 0 52px 0 52px;
  }
  .card__accent {
    position: absolute; left: 20px; top: 40px;
    width: 330px; height: 330px; border-radius: 50%;
    background: var(--teal-shade);
  }

  .brand { position: absolute; text-align: right; font-weight: 600; line-height: 1.05; }
  .brand__mark {
    position: absolute; left: 168px; top: 40px;
    width: 96px; height: 96px; border-radius: 50%;
    background: var(--blue-deep);
  }
  .brand--front { right: 27px; top: 168px; color: var(--teal-text); }
  .brand--back { right: 25px; top: 398px; color: var(--white); }
  .brand__name { display: block; font-size: 32px; letter-spacing: -0.3px; }
  .brand__tagline { display: block; font-size: 13px; margin-top: 2px; }

  .contact { position: absolute; left: 27px; top: 326px; color: var(--ink); }
  .contact__name { font-size: 17px; font-weight: 700; color: var(--teal-text); letter-spacing: 0.2px; line-height: 22px; }
  .contact__role { font-size: 14px; line-height: 18px; margin-top: 2px; }
  .contact__address { font-size: 13px; line-height: 15px; margin-top: 16px; }
  .contact__list { list-style: none; margin-top: 12px; font-size: 13px; }
  .contact__list li { display: flex; align-items: center; gap: 7px; height: 19px; }
  .contact__icon { width: 10px; height: 10px; fill: var(--teal-text); }
</style>
</head>
<body>
<main class="canvas">
  <section class="card card--front" aria-label="Card front">
    <span class="brand__mark" aria-hidden="true"></span>
    <div class="brand brand--front">
      <span class="brand__name">Bramblefield</span>
      <span class="brand__tagline">Growth Partners</span>
    </div>
    <div class="contact">
      <p class="contact__name">MALCOLM DERVANEY</p>
      <p class="contact__role">Owner</p>
      <p class="contact__address">58 Quorrin Ct,<br>Elmbridge Vic 3190</p>
      <ul class="contact__list">
        <li>
          <svg class="contact__icon" viewBox="0 0 10 10" aria-hidden="true">
            <path d="M1 3 Q5 0 9 3 L8 4.5 L6.5 3.8 L6.5 3 Q5 2.6 3.5 3 L3.5 3.8 L2 4.5 Z M2.5 5 H7.5 L8.5 9 H1.5 Z"/>
          </svg>
          <span>0418 923 047</span>
        </li>
        <li>
          <svg class="contact__icon" viewBox="0 0 10 10" aria-hidden="true">
            <path d="M0.5 2 H9.5 V8.5 H0.5 Z"/>
            <path d="M0.8 2.3 L5 5.6 L9.2 2.3" fill="none" stroke="#f2f2f2" stroke-width="0.9"/>
          </svg>
          <span>malcolm@bgp.com.au</span>
        </li>
      </ul>
    </div>
  </section>

  <section class="card card--back" aria-label="Card back">
    <span class="card__accent" aria-hidden="true"></span>
    <div class="brand brand--back">
      <span class="brand__name">Bramblefield</span>
      <span class="brand__tagline">Growth Partners</span>
    </div>
  </section>
</main>
</body>
</html>
```